Business Card design for a mini spa

business card for a small natural skincare/waxing spa. I need a modern, clean, classy card that draws people in but also need to be able to write future appointments on one side of it.

Target Market(s)

women age 16-70

Industry/Entity Type

Beauty Salon

Contact Information for Business Card

Brisk Skin Care 555-318-2956
2863 W Maltby Tarn, QX 40218
Facial, Waxing, Spray Tanning,

Colors
33b8a4

Requirements
Must have
• Brisk logo with flower
• my tag line "calm hands, bright days"
• 555-318-2956
• 2863 W Maltby
• a place to write ......Your Next Appointment
• Marta Quennell
Nice to have
• something modern, elegant, clean and simple with my attached logo. I also attached a few pictures of what I like along with a color pallet and a few fonts that I like.
Should not have
• no pictures of people in a spa I do not want your typical spa pictures like stone, people receiving a treatment.

```html
<!DOCTYPE html>
<html lang="en">
<head>
<meta charset="utf-8">
<title>Brisk Skin Care – Business Card</title>
<link href="https://fonts.googleapis.com/css2?family=Mulish:wght@200;300;400;500&family=Dancing+Script:wght@500&display=swap" rel="stylesheet">
<style>
  :root {
    --stage: #000000;
    --paper: #ffffff;
    --mint-light: #e4f3f2;
    --mint: #b9e2e0;
    --teal: #6fcbc8;
    --gold: #c6aa7f;
  }
  * { margin: 0; padding: 0; box-sizing: border-box; }
  html, body {
    width: 1200px; height: 1000px; overflow: hidden;
    background: var(--stage);
    font-family: "Mulish", "Helvetica Neue", Arial, sans-serif;
  }
  .canvas { position: relative; width: 1200px; height: 1000px; }

  .card {
    position: absolute; left: 258px; width: 683px; height: 390px; overflow: hidden;
  }

  /* Front */
  .card--front { top: 96px; }
  .front-pattern {
    position: absolute; inset: 0;
    background: radial-gradient(ellipse at 50% 45%, var(--mint-light) 0%, var(--mint) 100%);
  }
  .front-brand {
    position: absolute; left: 0; right: 0; top: 66px;
    text-align: center; color: var(--gold);
    font-weight: 200; font-size: 150px; letter-spacing: 6px; line-height: 1;
    padding-left: 6px;
  }
  .front-sub {
    position: absolute; left: 0; right: 0; top: 222px;
    text-align: center; color: var(--teal);
    font-weight: 200; font-size: 40px; letter-spacing: 3px; line-height: 1;
  }
  .front-rule {
    position: absolute; top: 243px; height: 3px; width: 71px; background: var(--teal);
  }
  .front-rule--left { left: 128px; }
  .front-rule--right { left: 474px; }
  .front-tagline {
    position: absolute; left: 0; right: 0; top: 272px; text-align: center;
    font-family: "Dancing Script", cursive; font-weight: 500;
    font-size: 44px; line-height: 1.1; color: var(--gold);
  }

  /* Back */
  .card--back { top: 522px; background: var(--paper); }
  .back-brand {
    position: absolute; left: 28px; top: 92px; width: 290px; text-align: center;
    font-weight: 200; line-height: 1;
  }
  .back-brand .brand-main {
    display: block; color: var(--teal);
    font-size: 90px; letter-spacing: 6px; padding-left: 6px;
  }
  .back-brand .brand-sub {
    display: block; color: var(--gold);
    font-size: 29px; letter-spacing: 2px; margin-top: 14px;
  }
  .back-divider {
    position: absolute; left: 341px; top: 68px; width: 2px; height: 168px; background: var(--gold);
  }
  .contact {
    position: absolute; left: 374px; top: 76px; font-style: normal; line-height: 1.3;
  }
  .contact-name { color: var(--gold); font-size: 25px; font-weight: 500; margin-bottom: 18px; }
  .contact-line { color: var(--teal); font-size: 23px; font-weight: 400; letter-spacing: 1px; }
  .contact-phone { margin-bottom: 8px; }

  .appointment {
    position: absolute; left: 35px; right: 35px; top: 288px;
  }
  .appointment-label {
    color: var(--teal); font-size: 21px; font-weight: 300;
    display: flex; align-items: flex-end; gap: 18px;
  }
  .write-line {
    flex: 1; border-bottom: 2px dotted var(--gold); height: 2px; margin-bottom: 6px;
  }
  .write-line--full { display: block; margin-top: 42px; }
</style>
</head>
<body>
<main class="canvas">

  <section class="card card--front" aria-label="Card front">
    <div class="front-pattern" role="img" aria-label="Soft mint background with a faint repeating flower pattern"></div>
    <h1 class="front-brand">BRISK</h1>
    <span class="front-rule front-rule--left"></span>
    <p class="front-sub">SKIN CARE</p>
    <span class="front-rule front-rule--right"></span>
    <p class="front-tagline">calm hands, bright days</p>
  </section>

  <section class="card card--back" aria-label="Card back">
    <h2 class="back-brand"><span class="brand-main">BRISK</span><span class="brand-sub">SKIN CARE</span></h2>
    <span class="back-divider"></span>
    <address class="contact">
      <p class="contact-name">Marta Quennell</p>
      <p class="contact-line contact-phone">555-318-2956</p>
      <p class="contact-line">2863 W Maltby Tarn<br>QX 40218</p>
    </address>
    <div class="appointment">
      <p class="appointment-label">NEXT APPOINTMENT <span class="write-line"></span></p>
      <span class="write-line write-line--full"></span>
    </div>
  </section>

</main>
</body>
</html>
```